Website Design for a Project Management Consulting Business

I have a logo design already and now I need a website.
I am a project manager and run my own consulting business.
Currently I am under contract with 3 major Vantage 400 companies. I'd like a website I can direct current and future clients.
My job is running IT projects and working with developers to deliver business priorities.
The website should be professional and clean - I work IT projects and would like to incorporate that into any theme.
I'd like the site to have several page or breakoff links - sections would include : about me, about my services, a page to display all of my certification badges, another page to talk about highlights from past projects and so on.
Looking for a collaborative experience.

Industry/Entity Type

Vantage 400 Consulting Firm - Project Management

Coding

Coded - Design and coding required

Number of Pages Required

1 page

Font styles to use
Serif

Colors
0094D4
00A9DD
6FCCEA
C7EBF8
E9F6FB
EE7325
F08F49
F5BC92
FAE3D3
FDF4ED

Requirements
Must have
• Sections that are a must: About Me (bio), About My Services, About my Certifications and Credentials, Experience on Past Projects,
Nice to have
• I have added the logo below - I'd like to use the logo and have it prominent ; should be professional and inviting

```html
<!DOCTYPE html>
<html lang="en">
<head>
<meta charset="UTF-8">
<title>Keystone Delivery Partners, LLC</title>
<link rel="stylesheet" href="https://fonts.googleapis.com/css2?family=Poppins:wght@400;500;600;700;800&display=swap">
<style>
:root{
  --blue:#0094d4;
  --blue-bright:#00a9dd;
  --blue-soft:#6fccea;
  --blue-pale:#c7ebf8;
  --blue-wash:#e9f6fb;
  --orange:#ee7325;
  --orange-soft:#f08f49;
  --navy:#0d3559;
  --ink:#2b2b2b;
  --text:#4a4a4a;
  --footer:#0b0b0b;
  --white:#ffffff;
}
*{box-sizing:border-box;margin:0;padding:0}
html,body{width:1200px;height:4083px;overflow:hidden}
body{font-family:"Poppins",sans-serif;color:var(--text);background:var(--white);position:relative}
.abs{position:absolute}

/* header */
.site-header{position:absolute;top:0;left:0;width:1200px;height:108px;background:var(--white)}
.brand{position:absolute;left:75px;top:30px;display:flex;align-items:center;gap:12px}
.brand-mark{width:40px;height:40px;background:var(--navy)}
.brand-name{font-size:20px;font-weight:700;color:var(--navy);line-height:1.05;letter-spacing:.5px}
.brand-name small{display:block;font-size:11px;font-weight:700;letter-spacing:2px}
.main-nav{position:absolute;right:72px;top:36px;display:flex;gap:36px;font-size:14px;font-weight:500;color:var(--navy);text-transform:uppercase}
.main-nav .active{color:var(--blue);position:relative}
.main-nav .active::after{content:"";position:absolute;right:-10px;top:-12px;width:14px;height:36px;border-top:2px solid var(--blue);border-right:2px solid var(--blue)}

/* hero */
.hero{position:absolute;top:108px;left:0;width:1200px;height:630px;background:linear-gradient(100deg,#3a3f46 0%,#5b5b5a 40%,#7a6a55 70%,#4a4a4c 100%)}
.hero-shade{position:absolute;inset:0;background:linear-gradient(90deg,rgba(20,25,35,.55),rgba(20,25,35,.1))}
.hero-title{position:absolute;left:75px;top:180px;font-size:46px;font-weight:800;color:var(--white);line-height:50px;text-transform:uppercase}
.hero-sub{position:absolute;left:75px;top:288px;width:560px;font-size:28px;color:var(--white);line-height:36px}
.btn-solid{position:absolute;left:75px;top:384px;width:195px;height:56px;background:var(--blue);color:var(--white);font-size:16px;font-weight:700;display:flex;align-items:center;justify-content:center;text-transform:uppercase}

.band{position:absolute;left:0;width:1200px;height:127px}

/* about */
.about-photo-frame-a{position:absolute;left:75px;top:955px;width:378px;height:328px;background:var(--blue-bright)}
.about-photo-frame-b{position:absolute;left:258px;top:1155px;width:358px;height:335px;background:var(--orange-soft)}
.about-photo{position:absolute;left:88px;top:968px;width:498px;height:490px;background:linear-gradient(160deg,#f4a9aa,#ef9b9c 60%,#e48c8f)}
.section-title{font-size:40px;font-weight:700;color:var(--ink);text-transform:uppercase;line-height:1.1}
.about-copy{position:absolute;left:675px;top:996px;width:460px}
.about-copy p{font-size:17px;line-height:30px;margin-top:24px}
.about-copy p+p{margin-top:22px}
.btn-outline{display:inline-flex;align-items:center;justify-content:center;border:2px solid var(--blue);color:var(--blue);font-size:16px;font-weight:700;text-transform:uppercase;height:58px;padding:0 24px}
.about-copy .btn-outline{margin-top:30px}

/* services */
.services{position:absolute;top:1708px;left:0;width:1200px;height:745px;background:var(--blue-wash)}
.services-intro{position:absolute;left:75px;top:250px;width:410px}
.services-intro p{font-size:17px;line-height:30px;margin-top:24px}
.services-intro .btn-outline{margin-top:36px;padding:0 14px}
.service-card{position:absolute;width:295px;background:var(--white);padding:24px 22px}
.service-card h3{font-size:21px;font-weight:700;color:var(--blue);line-height:27px;text-transform:uppercase;margin-top:14px}
.service-card p{font-size:15px;line-height:27px;margin-top:12px;color:var(--text)}
.card-blue{left:525px;top:75px;height:285px;border-top:5px solid var(--blue-bright);border-right:5px solid var(--blue-bright)}
.card-orange{left:520px;top:376px;height:285px;border-top:5px solid var(--orange-soft);border-left:5px solid var(--orange-soft)}
.card-dark{left:837px;top:234px;height:282px;border-right:5px solid #3a3a3a;border-bottom:5px solid #3a3a3a}
.service-icon{width:78px;height:74px}

/* projects */
.projects{position:absolute;top:2453px;left:0;width:1200px;height:657px;background:var(--white)}
.projects .section-title{position:absolute;left:75px;top:94px}
.slider-arrows{position:absolute;right:72px;top:96px;display:flex;gap:28px}
.project-card{position:absolute;top:190px;width:328px;height:324px;color:var(--white);text-align:center;overflow:hidden}
.project-card .shade{position:absolute;inset:0;background:linear-gradient(180deg,rgba(0,0,0,0) 40%,rgba(0,0,0,.75) 100%)}
.project-card h4{position:absolute;left:0;right:0;top:220px;font-size:21px;font-weight:700;text-transform:uppercase}
.project-card p{position:absolute;left:40px;right:40px;top:254px;font-size:15px;line-height:23px}
.p1{left:75px;background:linear-gradient(150deg,#4a4e55,#25282d 60%,#3b3b3b)}
.p2{left:437px;background:linear-gradient(150deg,#d9dde0,#9aa6ae 50%,#4e5458)}
.p3{left:799px;background:linear-gradient(150deg,#5a4a40,#3a2f2a 55%,#23262b)}
.dots{position:absolute;top:568px;left:556px;display:flex;gap:17px}
.dots span{width:10px;height:10px;border-radius:50%;background:#9aa3a8}
.dots span.on{background:var(--blue)}

/* certifications */
.certs{position:absolute;top:3110px;left:0;width:1200px;height:730px;background:var(--blue-wash)}
.certs .section-title{position:absolute;left:0;right:0;top:76px;text-align:center}
.certs-lead{position:absolute;left:110px;right:110px;top:142px;text-align:center;font-size:17px;line-height:29px}
.cert-visual{position:absolute;left:38px;top:220px;width:470px;height:385px;background:linear-gradient(135deg,#1f3a7a,#d8b24a 30%,#f7f7f5 45%,#f7f7f5 70%,#d8b24a 85%,#1f3a7a);transform:rotate(-4deg);box-shadow:0 20px 30px rgba(0,0,0,.15)}
.cert-list{position:absolute;left:524px;top:218px;width:580px;list-style:none}
.cert-list li{display:flex;gap:28px;margin-bottom:22px;min-height:106px}
.cert-num{flex:0 0 64px;height:64px;border-radius:50%;background:var(--blue-bright);color:var(--white);font-size:28px;font-weight:700;display:flex;align-items:center;justify-content:center;margin-top:10px}
.cert-list h5{font-size:21px;font-weight:600;color:var(--blue-bright);line-height:30px}
.cert-list p{font-size:17px;line-height:29px}
.certs .btn-outline{position:absolute;left:524px;top:604px;width:196px}

/* footer */
.site-footer{position:absolute;top:3840px;left:0;width:1200px;height:243px;background:var(--footer);color:var(--white);text-align:center}
.footer-nav{display:flex;justify-content:center;gap:46px;margin-top:78px;font-size:15px;font-weight:500;text-transform:uppercase}
.copyright{font-size:14px;margin-top:14px}
.social{display:flex;justify-content:center;gap:22px;margin-top:16px}
.social span{width:22px;height:22px;background:#d9d9d9;border-radius:4px}
</style>
</head>
<body>

<header class="site-header">
  <div class="brand">
    <span class="brand-mark"></span>
    <span class="brand-name">KEYSTONE DELIVERY<small>PARTNERS, LLC</small></span>
  </div>
  <nav class="main-nav">
    <span class="active">Home</span>
    <span>About Me</span>
    <span>My Services</span>
    <span>Past Projects</span>
    <span>Certifications</span>
    <span>Contact Me</span>
  </nav>
</header>

<section class="hero" role="img" aria-label="Team of developers reviewing code on computer screens in an office">
  <div class="hero-shade"></div>
  <h1 class="hero-title">Keystone Delivery<br>Partners, LLC</h1>
  <p class="hero-sub">I am a project manager and run my own consulting business.</p>
  <span class="btn-solid">More About Me</span>
</section>

<svg class="band" style="top:738px" viewBox="0 0 1200 127" preserveAspectRatio="none">
  <polygon points="0,0 1200,0 1200,127 0,6" fill="#c7ebf8"/>
  <polygon points="0,8 555,66 0,127" fill="#0094d4"/>
</svg>

<section class="about">
  <div class="about-photo-frame-a"></div>
  <div class="about-photo-frame-b"></div>
  <div class="about-photo" role="img" aria-label="Portrait of the consultant in a blue shirt with arms crossed"></div>
  <div class="about-copy">
    <h2 class="section-title">About Me</h2>
    <p>Daniel Whitcomb is the Owner of Keystone Delivery Partners, LLC and serves as Principal Lead Consultant on waterfall and agile contract opportunities.</p>
    <p>Keystone Delivery Partners, LLC has engaged on a contract basis with Vantage 400 companies across various industries including banking and credit unions, global supply chain, and international food distribution.</p>
    <span class="btn-outline">More About Me</span>
  </div>
</section>

<svg class="band" style="top:1583px" viewBox="0 0 1200 127" preserveAspectRatio="none">
  <polygon points="0,0 1200,116 1200,127 0,127" fill="#e9f6fb"/>
  <polygon points="0,0 1200,116 1200,127 0,127" fill="#c7ebf8"/>
  <polygon points="650,60 1200,0 1200,110" fill="#0094d4"/>
</svg>

<section class="services">
  <div class="services-intro">
    <h2 class="section-title">About My Services</h2>
    <p>Daniel Whitcomb has extensive experience in leading projects and initiatives for business teams and IT/IS teams alike. Highlights are below:</p>
    <span class="btn-outline">View All Services</span>
  </div>

  <article class="service-card card-blue">
    <svg class="service-icon" viewBox="0 0 78 74" fill="none" stroke="#222" stroke-width="2.2">
      <rect x="2" y="2" width="56" height="62" rx="3"/>
      <line x1="2" y1="12" x2="58" y2="12"/>
      <rect x="9" y="20" width="8" height="8"/><line x1="22" y1="24" x2="46" y2="24"/>
      <rect x="9" y="34" width="8" height="8"/><line x1="22" y1="38" x2="40" y2="38"/>
      <rect x="9" y="48" width="8" height="8"/><line x1="22" y1="52" x2="36" y2="52"/>
      <circle cx="60" cy="56" r="15" fill="#fff"/>
      <polyline points="53,56 58,61 67,51"/>
    </svg>
    <h3>Senior Scaleflow Scrum Master</h3>
    <p>Charged with leading Scaleflow agile scrum teams consisting of various Mainframe.</p>
  </article>

  <article class="service-card card-orange">
    <svg class="service-icon" viewBox="0 0 78 74" fill="none" stroke="#222" stroke-width="2.2">
      <circle cx="38" cy="12" r="8"/>
      <path d="M26 34c0-8 6-13 12-13s12 5 12 13"/>
      <rect x="4" y="40" width="22" height="30"/>
      <line x1="9" y1="48" x2="21" y2="48"/><line x1="9" y1="55" x2="21" y2="55"/><line x1="9" y1="62" x2="21" y2="62"/>
      <circle cx="58" cy="56" r="10"/><circle cx="58" cy="56" r="4"/>
      <polyline points="30,56 44,56"/><polyline points="34,52 30,56 34,60"/>
    </svg>
    <h3>Senior Project Manger</h3>
    <p>Charged with leading Scaleflow agile scrum teams consisting of various Mainframe.</p>
  </article>

  <article class="service-card card-dark">
    <svg class="service-icon" viewBox="0 0 78 74" fill="none" stroke="#222" stroke-width="2.2">
      <circle cx="30" cy="26" r="11"/>
      <path d="M8 72c0-14 10-24 22-24s22 10 22 24"/>
      <circle cx="56" cy="18" r="12"/><circle cx="56" cy="18" r="5"/>
      <line x1="56" y1="2" x2="56" y2="6"/><line x1="56" y1="30" x2="56" y2="34"/>
      <line x1="40" y1="18" x2="44" y2="18"/><line x1="68" y1="18" x2="72" y2="18"/>
    </svg>
    <h3>Senior Program Manger</h3>
    <p>Charged with leading Scaleflow agile scrum teams consisting of various Mainframe.</p>
  </article>
</section>

<section class="projects">
  <h2 class="section-title">Experience on Past Projects</h2>
  <div class="slider-arrows">
    <svg width="20" height="32" viewBox="0 0 20 32" fill="none" stroke="#333" stroke-width="2.5"><polyline points="17,2 3,16 17,30"/></svg>
    <svg width="20" height="32" viewBox="0 0 20 32" fill="none" stroke="#0094d4" stroke-width="2.5"><polyline points="3,2 17,16 3,30"/></svg>
  </div>
  <article class="project-card p1" role="img" aria-label="Laptop keyboard with code on screen">
    <div class="shade"></div>
    <h4>Project Heading</h4>
    <p>Nemo enim ipsam voluptatem quia voluptas.</p>
  </article>
  <article class="project-card p2" role="img" aria-label="Designer at a desk planning app screens on a monitor">
    <div class="shade"></div>
    <h4>Project Heading</h4>
    <p>Nemo enim ipsam voluptatem quia voluptas.</p>
  </article>
  <article class="project-card p3" role="img" aria-label="Developer working at multiple monitors with code">
    <div class="shade"></div>
    <h4>Project Heading</h4>
    <p>Nemo enim ipsam voluptatem quia voluptas.</p>
  </article>
  <div class="dots"><span class="on"></span><span></span><span></span><span></span></div>
</section>

<section class="certs">
  <h2 class="section-title">Certifications and Credentials</h2>
  <p class="certs-lead">Sed ut perspiciatis unde omnis iste natus error sit voluptatem accusantium doloremque laudantium, totam rem aperiam, eaque ipsa quae ab illo inventore veritatis et quasi architecto.</p>
  <div class="cert-visual" role="img" aria-label="Framed certificate of appreciation with gold and navy border"></div>
  <ol class="cert-list">
    <li><span class="cert-num">1</span><div><h5>Organization:</h5><p>PLI - Project Leadership Institute - Certifications: Certified Delivery Professional (CDP), and PLI-AP (Agile Practitioner)</p></div></li>
    <li><span class="cert-num">2</span><div><h5>Organization:</h5><p>AgileGuild - Certifications: Certified Sprint Lead (CSL), Advanced Certified Sprint Lead (A-CSL), Certified Backlog Owner (CBO)</p></div></li>
    <li><span class="cert-num">3</span><div><h5>Organization:</h5><p>Scaleflow Institute - Certifications: Scaleflow Team Coach (STC), Scaleflow Leader (SL)</p></div></li>
  </ol>
  <span class="btn-outline">Read More</span>
</section>

<footer class="site-footer">
  <nav class="footer-nav">
    <span>Home</span><span>About Me</span><span>My Services</span><span>Past Projects</span><span>Certifications</span><span>Contact Me</span>
  </nav>
  <p class="copyright">Copyright © 2022 Company Name All Rights Reserved.</p>
  <div class="social" aria-label="Social media links">
    <span></span><span></span><span></span><span></span><span></span>
  </div>
</footer>

</body>
</html>
```